Business Card Design Project

Looking for a logo and business card for a Real State Business i will be opening. The name is not choosen yet , but will probably be RWT IMOVEIS.
I was thinking black and silver colors, but am open to nice ideas.
I did add a business card that i liked a lot, am looking for something like that, with logo in black or silver in a black card. The logo i was thinking in the letters RWT as i uploaded or something or little and cute buildings or a house...just ideas, can be any nice logo.
Updates

You guys can add other colors if you want, I like colors very "BRIGHT" and "open", like red, pink, strong colors. almost glow in the dark colors. lol

Designers,

I've increased more 88 dollars in the budget for 1st place cause I will want envelope designs... small and big sizes.

So 1st place is now U$248,00. 

No need to send the envelope designs right now... only the business cards designs.

Thank you.

Industry/Entity Type

Business

Requirements
Must have
• Marcela Tavares Rocha

www.RWTimoveis-exemplo.com.br

+554187316042

marcela@rwtimoveis-exemplo.com.br

```html
<!DOCTYPE html>
<html lang="pt-BR">
<head>
<meta charset="utf-8">
<title>RWT Imoveis – Business Cards</title>
<link rel="stylesheet" href="https://fonts.googleapis.com/css2?family=Montserrat:wght@500&display=swap">
<style>
  :root {
    --backdrop: #3a3330;
    --card-black: #151515;
    --card-edge: #0b0b0b;
    --gloss-black: #2e2e2e;
    --silver: #e6e6e6;
    --silver-soft: #bdbdbd;
    --band-light: #cfcfcf;
    --band-dark: #1c1c1c;
  }
  * { margin: 0; padding: 0; box-sizing: border-box; }
  html, body {
    width: 1200px;
    height: 716px;
    overflow: hidden;
    background: var(--backdrop);
  }
  .canvas {
    width: 1200px;
    height: 716px;
    display: flex;
    align-items: center;
    justify-content: center;
    gap: 60px;
    font-family: "Montserrat", sans-serif;
    font-weight: 500;
  }
  .card {
    position: relative;
    width: 500px;
    height: 286px;
    background: var(--card-black);
    border: 1px solid var(--card-edge);
    box-shadow: 0 18px 40px rgba(0,0,0,0.45);
    overflow: hidden;
  }
  /* Front */
  .card-front {
    display: flex;
    align-items: center;
    justify-content: center;
  }
  .front-name {
    font-size: 38px;
    letter-spacing: 2px;
    color: var(--gloss-black);
    white-space: nowrap;
  }
  /* Back */
  .silver-band {
    position: absolute;
    left: 0;
    right: 0;
    top: 102px;
    height: 44px;
    background: linear-gradient(90deg, var(--band-light) 0%, #8d8d8d 35%, #3a3a3a 60%, var(--band-dark) 85%);
  }
  .back-content {
    position: absolute;
    left: 225px;
    top: 58px;
    width: 255px;
  }
  .back-name {
    font-size: 22px;
    line-height: 30px;
    letter-spacing: 1px;
    color: var(--silver);
    white-space: nowrap;
  }
  .holder-name {
    margin-top: 70px;
    font-size: 12px;
    line-height: 16px;
    letter-spacing: 1px;
    color: var(--silver);
    white-space: nowrap;
  }
  .contact-list {
    list-style: none;
    margin-top: 12px;
    font-size: 9.5px;
    line-height: 17px;
    letter-spacing: 0.6px;
    color: var(--silver-soft);
    text-transform: uppercase;
    white-space: nowrap;
  }
  .contact-list .phone { color: var(--silver); }
</style>
</head>
<body>
<main class="canvas">
  <section class="card card-front" aria-label="Business card front">
    <span class="front-name">RWT IMOVEIS</span>
  </section>

  <section class="card card-back" aria-label="Business card back">
    <div class="silver-band" role="img" aria-label="Silver band fading from light to dark across the card"></div>
    <div class="back-content">
      <div class="back-name">RWT IMOVEIS</div>
      <div class="holder-name">Marcela Tavares Rocha</div>
      <ul class="contact-list">
        <li class="phone">+554187316042</li>
        <li>marcela@rwtimoveis-exemplo.com.br</li>
        <li>www.RWTimoveis-exemplo.com.br</li>
      </ul>
    </div>
  </section>
</main>
</body>
</html>
```